Business card for law firm

Need business card for new law firm. Think confident, authoritative, conservative, but not stuffy or old-fashioned.

Contact Information for Business Card

Content for card - logo (uploaded), plus the following:

Paul Whitcombe (larger font)
Managing Partner (larger font, but not as large as name)
Level 9, 7 Ferris Lane
Sydney NSW 2000
Main Tel 02 9364 2710
Direct Tel 02 8472 3159
Email paul@qvlegal.com.au
www.qvlegal.com.au

Letterhead design should include logo plus:
Level 9, 7 Ferris Lane
Sydney NSW 2000
Tel 02 8472 3159
www.qvlegal.com.au

```html
<!DOCTYPE html>
<html lang="en">
<head>
<meta charset="utf-8">
<title>Quayvale Legal – Business Card</title>
<link rel="stylesheet" href="https://fonts.googleapis.com/css2?family=Cinzel:wght@400;500&family=Open+Sans:wght@400&display=swap">
<style>
  :root {
    --backdrop: #5b5b5b;
    --card-light: #f3f3f3;
    --navy: #0b2160;
    --navy-soft: #13296b;
    --ink: #151515;
    --white: #ffffff;
  }
  * { margin: 0; padding: 0; box-sizing: border-box; }
  html, body { width: 1200px; height: 900px; overflow: hidden; }
  body { background: var(--backdrop); position: relative; font-family: "Open Sans", Arial, sans-serif; }

  .card { position: absolute; top: 200px; width: 310px; height: 502px; overflow: hidden; }

  .card--front {
    left: 253px;
    background: var(--card-light);
    border-radius: 56px 0 56px 0;
  }
  .card--back {
    left: 627px;
    background: var(--navy);
    border-radius: 0 56px 0 56px;
  }

  .brand { position: absolute; left: 0; right: 0; text-align: center; font-family: "Cinzel", Georgia, serif; font-weight: 400; }
  .brand__mark { display: block; width: 26px; height: 26px; margin: 0 auto 34px; background: var(--navy); }
  .brand__name { display: block; font-size: 37px; line-height: 1; letter-spacing: 1px; }
  .brand__sub { display: block; font-size: 14px; letter-spacing: 10px; margin-top: 8px; padding-left: 10px; }

  .card--front .brand { top: 96px; color: var(--ink); }
  .card--back .brand { top: 376px; color: var(--white); }

  .back-field {
    position: absolute; inset: 0;
    background: linear-gradient(150deg, var(--navy) 0%, var(--navy-soft) 45%, var(--navy) 100%);
  }

  .contact { position: absolute; left: 33px; top: 306px; color: var(--ink); }
  .contact__name { font-family: "Cinzel", Georgia, serif; font-weight: 500; font-size: 19px; color: var(--navy); line-height: 1.1; letter-spacing: 0.3px; }
  .contact__role { font-size: 14.5px; line-height: 1.2; margin-bottom: 7px; }
  .contact__list { list-style: none; font-size: 14px; line-height: 18px; }
  .contact__list li { display: flex; align-items: center; gap: 3px; }
  .contact__list svg { width: 11px; height: 11px; fill: var(--navy); flex: none; }
  .contact__note { font-size: 12px; }
  .contact__address { font-style: normal; font-size: 14px; line-height: 18px; margin-top: 6px; }
</style>
</head>
<body>

  <section class="card card--front" aria-label="Card front">
    <div class="brand">
      <span class="brand__mark" aria-hidden="true"></span>
      <span class="brand__name">QUAYVALE</span>
      <span class="brand__sub">LEGAL</span>
    </div>

    <div class="contact">
      <p class="contact__name">PAUL WHITCOMBE</p>
      <p class="contact__role">Managing Partner</p>
      <ul class="contact__list">
        <li><svg viewBox="0 0 12 12" aria-hidden="true"><path d="M1 4c0-2 2-3 5-3s5 1 5 3l-2 1-1-2H4L3 5zM3 6h6l2 5H1z"/></svg>02 9364 2710</li>
        <li><svg viewBox="0 0 12 12" aria-hidden="true"><path d="M1 4c0-2 2-3 5-3s5 1 5 3l-2 1-1-2H4L3 5zM3 6h6l2 5H1z"/></svg>02 8472 3159 <span class="contact__note">(DIRECT)</span></li>
        <li><svg viewBox="0 0 12 12" aria-hidden="true"><path d="M1 3h10v7H1zM1.5 3.5 6 7l4.5-3.5"/></svg>paul@qvlegal.com.au</li>
        <li><svg viewBox="0 0 12 12" aria-hidden="true"><circle cx="6" cy="6" r="5"/></svg>www.qvlegal.com.au</li>
      </ul>
      <address class="contact__address">Level 9, 7 Ferris Lane<br>Sydney NSW 2000</address>
    </div>
  </section>

  <section class="card card--back" aria-label="Card back">
    <div class="back-field" role="img" aria-label="Large faint brand symbol sweeping across the navy background"></div>
    <div class="brand">
      <span class="brand__name">QUAYVALE</span>
      <span class="brand__sub">LEGAL</span>
    </div>
  </section>

</body>
</html>
```